Book cover

I need a cover for a my 3rd book that kinda goes with my brand (my previous book. The name of my first book - "Turbulence Behind the Yoke" Hidden Strain Inside Modern Cockpits: A Guide for Travelers". In the same style I need my third book - NO HARBOR" to stand out. I need a bolder, less whimsy cover, less playful. So can we use some of the same elements to stay consistent in this book cover. Perhaps use text to envoke emotions. This is the back cover so far (see below attachemnent)

Hello,
Subject: Cover Direction & Brand Consistency

Hi everyone,

Here’s my honest take: I don’t think the current execution fully reflects my brand yet. What I’m wondering is whether we can bring more continuity across my books—borrowing elements from my first and second covers to inform this third one. Think of how authors like Dorian Welk maintain a recognizable style across their work. That consistency builds trust and signals authority before a reader even opens the book. Design choices like this matter more than we realize.

I’ve attached a cover I came across on Brindlemart that reminded me of Option 5 and feels aligned with where you’re headed. One thought: could we experiment with introducing a crack—or cracks—into the word HARBOR itself? Maybe put the title "NO HARBOR" at the edge of the cover vertically?

Curious to hear your thoughts and how you see this evolving.
P.s. Is there away to attach an idea?

NO HARBOR: Restoring Quiet Edges in a Culture that Praises Hurry

```html
<!DOCTYPE html>
<html lang="en">
<head>
<meta charset="UTF-8">
<title>No Harbor — Book Cover Wrap</title>
<link rel="stylesheet" href="https://fonts.googleapis.com/css2?family=Montserrat:wght@400;500;600;700&family=Roboto:wght@400;700&family=Roboto+Condensed:wght@700&family=Archivo+Black&display=swap">
<style>
  :root {
    --navy: #1b2533;
    --navy-deep: #0f1724;
    --sky-blue: #1eb4e6;
    --steel: #2c7ca3;
    --teal-dark: #0d4c6e;
    --cloud: #c9dbe6;
    --paper: #ffffff;
    --body-text: #f2f4f7;
  }
  * { margin: 0; padding: 0; box-sizing: border-box; }
  html, body { width: 1200px; height: 882px; overflow: hidden; background: var(--navy-deep); }
  .wrap { position: relative; width: 1200px; height: 882px; overflow: hidden; font-family: "Montserrat", sans-serif; }

  /* Back cover */
  .back {
    position: absolute; left: 0; top: 0; width: 585px; height: 882px;
    background: linear-gradient(180deg, var(--navy) 0%, #18212e 65%, var(--navy-deep) 100%);
  }
  .back-headline {
    position: absolute; left: 37px; top: 40px; width: 500px;
    color: var(--sky-blue); font-weight: 600; font-size: 18.5px; line-height: 18px;
  }
  .back-blurb {
    position: absolute; left: 37px; top: 125px; width: 484px;
    color: var(--body-text); font-size: 12.4px; line-height: 17.75px; text-align: justify;
  }
  .bio {
    position: absolute; left: 37px; top: 551px; width: 378px;
    color: var(--body-text); font-size: 10.6px; line-height: 12.7px;
  }
  .bio p:first-child { text-align: justify; }
  .bio strong { font-weight: 700; }
  .author-photo { position: absolute; left: 423px; top: 557px; width: 96px; height: 130px; }
  .publisher {
    position: absolute; left: 38px; top: 810px; display: flex; align-items: center; gap: 5px;
    color: #c9a24a; font-weight: 600; font-size: 9.5px; letter-spacing: 1px;
  }
  .publisher-dot { width: 9px; height: 9px; border-radius: 50%; background: #c9a24a; }
  .price {
    position: absolute; left: 212px; top: 816px;
    color: var(--paper); font-family: "Roboto Condensed", sans-serif; font-weight: 700; font-size: 9.5px; line-height: 14px;
  }

  /* Spine */
  .spine {
    position: absolute; left: 578px; top: 0; width: 60px; height: 882px;
    background: linear-gradient(90deg, var(--navy) 0%, #233a4e 55%, #4a7a95 100%);
  }
  .spine-text {
    position: absolute; left: 609px; top: 58px; transform-origin: 0 0; transform: rotate(90deg);
    white-space: nowrap; color: var(--paper); font-family: "Roboto", sans-serif; font-size: 13.5px; letter-spacing: 0.2px;
  }
  .spine-author { top: 624px; }

  /* Front cover */
  .front-art { position: absolute; left: 620px; top: 0; width: 580px; height: 882px; }
  .title-stack {
    position: absolute; left: 1078px; top: 72px; width: 80px;
    display: flex; flex-direction: column; align-items: center;
    color: var(--paper); font-family: "Archivo Black", sans-serif; font-size: 84px; line-height: 80px;
  }
  .title-gap { height: 44px; }
  .front-subtitle {
    position: absolute; left: 643px; top: 458px; width: 420px;
    color: var(--paper); font-family: "Roboto Condensed", sans-serif; font-weight: 700; font-size: 53px; line-height: 56px; letter-spacing: -0.5px;
  }
  .front-author {
    position: absolute; left: 643px; top: 700px;
    color: var(--sky-blue); font-family: "Roboto Condensed", sans-serif; font-weight: 700; font-size: 30px;
  }
</style>
</head>
<body>
<div class="wrap">

  <section class="back">
    <h2 class="back-headline">Women have been told we could do and be anything … and we can.<br>What’s rarely mentioned is the toll on our health, relationships, and overall wellbeing.</h2>

    <div class="back-blurb">
      <p>Are you the woman who holds it all together—crushing deadlines, leading teams, raising a family—while quietly unraveling inside? Yes, you are competent and capable. You’ve simply been carrying more than you were ever meant to for too long.</p>
      <p>No Harbor offers a different way forward. Drawn from decades of experience flying commercial aircraft and championing women's health, retired Captain Marielle Thornquist reveals the missing skill most high-achieving women were never taught: protecting your margins in a world that glorifies overload. This vital buffer not only enables recovery after near-collapse, but also prevents you from reaching the breaking point of exhaustion.</p>
      <p>You will learn about the centuries-old mindset when humans first became cogs in the machine, the science of burnout and brain rewiring, the psychology driving us to push limits, and the cultural systems rigged against women. Discover how to spot the three stages of depletion before they ground you. Through self-assessment tools and actionable practices, the author guides us back home to ourselves by offering a roadmap to rebuild our strength, reconnect with joy and purpose, and redefine success to include true wellbeing.</p>
      <p>You don’t need to crash to earn a soft landing. Buckle up! No Harbor is your wakeup call to fly lighter and higher than you ever imagined.</p>
      <p>Marielle Thornquist is a speaker, consultant, and founder of the Airborne Vitality Institute. With over 10,000 flight hours, she now empowers women to successfully lead without losing themselves.</p>
    </div>

    <div class="bio">
      <p><strong>CAPTAIN MARIELLE THORNQUIST</strong> is the founder of Steady Wing Wellness, an aviation-based wellbeing organization that builds on her 34+ years of experience as a commercial airline pilot. She helps others in high-performance professions and those seeking careers as airline pilots achieve a healthier, more rewarding life using practical techniques tailored for their careers. She currently captains W-400 aircrafts and has logged over 10,000 hours of jet flight time.</p>
      <p>Marielle has over a decade of experience in health and wellbeing as an aviation strategist. She is certified in Mindfulness Based Stress Reduction (MBSR) at Halvern University and earned a BS in Leadership (Delta Lyra Honor Society) and an Executive Certificate in Business from Coastridge University.</p>
      <p>Having travelled the globe repeatedly, Marielle's favorite place in the world is with her family, spending time on the east and west coast of the US. She enjoys gardening, meditation, and the love of learning.</p>
    </div>

    <svg class="author-photo" viewBox="0 0 96 130" role="img" aria-label="Author portrait in captain's uniform in front of a jet engine">
      <defs>
        <linearGradient id="photoTone" x1="0" y1="0" x2="0" y2="1">
          <stop offset="0" stop-color="#1c1f24"/>
          <stop offset="0.55" stop-color="#6f757c"/>
          <stop offset="1" stop-color="#9a8e82"/>
        </linearGradient>
      </defs>
      <rect width="96" height="130" fill="url(#photoTone)"/>
    </svg>

    <div class="publisher"><span class="publisher-dot"></span>EMBERLINE PRESS</div>
    <div class="price">US $19.99<br>CA $23.99</div>
  </section>

  <div class="spine"></div>
  <div class="spine-text">NO HARBOR: Restoring Quiet Edges in a Culture that Praises Hurry</div>
  <div class="spine-text spine-author">Capt. Marielle Thornquist</div>

  <section class="front">
    <svg class="front-art" viewBox="0 0 580 882" preserveAspectRatio="none" role="img" aria-label="Motion-blurred blue sky with a shattered glass impact at centre">
      <defs>
        <linearGradient id="skyBase" x1="0" y1="0" x2="0" y2="1">
          <stop offset="0" stop-color="#2f6f90"/>
          <stop offset="0.3" stop-color="#3b86ad"/>
          <stop offset="0.55" stop-color="#2a7aa3"/>
          <stop offset="0.8" stop-color="#7c96a8"/>
          <stop offset="1" stop-color="#0d4c6e"/>
        </linearGradient>
        <radialGradient id="skyGlow" cx="0.35" cy="0.45" r="0.6">
          <stop offset="0" stop-color="#c9dbe6" stop-opacity="0.55"/>
          <stop offset="1" stop-color="#c9dbe6" stop-opacity="0"/>
        </radialGradient>
        <linearGradient id="spineBlend" x1="0" y1="0" x2="1" y2="0">
          <stop offset="0" stop-color="#4a7a95" stop-opacity="1"/>
          <stop offset="0.08" stop-color="#4a7a95" stop-opacity="0"/>
        </linearGradient>
      </defs>
      <rect width="580" height="882" fill="url(#skyBase)"/>
      <rect width="580" height="882" fill="url(#skyGlow)"/>
      <rect width="580" height="882" fill="url(#spineBlend)"/>
    </svg>

    <h1 class="title-stack" aria-label="No Harbor">
      <span>N</span><span>O</span><span class="title-gap"></span>
      <span>H</span><span>A</span><span>R</span><span>B</span><span>O</span><span>R</span>
    </h1>

    <p class="front-subtitle">Restoring Quiet Edges in a Culture that Praises Hurry</p>
    <p class="front-author">Capt. Marielle Thornquist</p>
  </section>

</div>
</body>
</html>
```